Luxury Business Card Design for High-End Window Treatments

Gilded Slatworks
Custom Plantation Shutters & Architectural Shading Systems

⸻

BACK

Daniel Trevick
Owner

Custom Interior & Exterior Window Treatments

919-555-0148
gildedslatworks.com

I have included a picture that I’m hoping we can use on the back, but I’m also wondering if you can get rid of the ladder? Should we get rid of shutters , shades and blinds underneath Gilded Slatworks?

Target Market(s)

High-end residential homeowners, custom home builders, architects, interior designers, and luxury renovation clients seeking premium plantation shutters and motorized architectural shading systems.

Industry/Entity Type

Custom Window treatments

Contact Information for Business Card

Front Gilded Slatworks Custom Plantation Shutters Motorized Architectural Shading Systems BACK Daniel Trevick Owner 919-555-0148 GildedSlatworks.com Custom Interior & Exterior Window Treatments By Appointment

Requirements
Nice to have
• Not 100% sure on nice to halves or the color but you can definitely check out my website to get a better understanding of what I’m trying to do

```html
<!DOCTYPE html>
<html lang="en">
<head>
<meta charset="utf-8">
<title>Gilded Slatworks — Business Card</title>
<link href="https://fonts.googleapis.com/css2?family=Cormorant+Garamond:wght@500;600&family=Great+Vibes&family=Questrial&display=swap" rel="stylesheet">
<style>
  :root {
    --backdrop: #2b2b2d;
    --card-black: #050505;
    --card-white: #ffffff;
    --gold: #b89a3e;
    --gold-light: #d6bd68;
    --ink: #1a1a1a;
    --tag-white: #f4f1ea;
    --sky: #9cc3e6;
    --siding: #c9c3b3;
    --screen: #3a4250;
    --foliage: #4e6a3a;
  }
  * { box-sizing: border-box; margin: 0; padding: 0; }
  html, body { width: 1200px; height: 689px; overflow: hidden; }
  body {
    background: var(--backdrop);
    position: relative;
    font-family: "Cormorant Garamond", serif;
  }
  .card {
    position: absolute;
    top: 190px;
    width: 540px;
    height: 309px;
    border-radius: 18px;
    overflow: hidden;
    box-shadow: 0 0 0 2px var(--gold), 0 18px 40px rgba(0,0,0,.45);
  }

  /* Front */
  .card-front { left: 30px; background: var(--card-black); }
  .brand-name {
    position: absolute;
    left: 0; right: 0; top: 58px;
    text-align: center;
    color: var(--gold-light);
    font-weight: 600;
    font-size: 58px;
    line-height: 0.95;
  }
  .brand-tagline {
    position: absolute;
    left: 0; right: 0; top: 196px;
    text-align: center;
    color: var(--tag-white);
    font-weight: 500;
    font-size: 19px;
    line-height: 1.2;
  }

  /* Back */
  .card-back { left: 630px; background: var(--card-white); }
  .back-photo {
    position: absolute;
    inset: 0 0 0 150px;
    background:
      linear-gradient(180deg, var(--sky) 0%, var(--sky) 14%, transparent 30%),
      linear-gradient(180deg, var(--siding) 0%, var(--screen) 45%, var(--siding) 62%, var(--foliage) 82%, #7b8463 100%);
    -webkit-mask-image: linear-gradient(90deg, transparent 0%, rgba(0,0,0,.35) 30%, #000 62%);
    mask-image: linear-gradient(90deg, transparent 0%, rgba(0,0,0,.35) 30%, #000 62%);
  }
  .owner-name {
    position: absolute;
    left: 34px; top: 28px;
    font-family: "Great Vibes", cursive;
    color: var(--gold);
    font-size: 46px;
    line-height: 1;
  }
  .owner-role {
    position: absolute;
    left: 40px; top: 82px;
    font-family: "Questrial", sans-serif;
    color: var(--ink);
    font-size: 17px;
  }
  .contact-list {
    position: absolute;
    left: 40px; top: 130px;
    list-style: none;
    font-family: "Questrial", sans-serif;
    color: var(--ink);
    font-size: 19px;
  }
  .contact-list li { display: flex; align-items: center; gap: 10px; height: 30px; }
  .contact-list svg { width: 18px; height: 18px; fill: var(--gold); }
  .service-lines {
    position: absolute;
    left: 40px; top: 216px;
    color: var(--gold);
    font-weight: 500;
    font-size: 19px;
    line-height: 1.15;
  }
</style>
</head>
<body>
  <section class="card card-front" aria-label="Card front">
    <h1 class="brand-name">Gilded<br>Slatworks</h1>
    <p class="brand-tagline">Gilded Slatworks Custom<br>Plantation Shutters Motorized<br>Architectural Shading Systems</p>
  </section>

  <section class="card card-back" aria-label="Card back">
    <div class="back-photo" role="img" aria-label="Photo of a two-storey home with screened porches, white columns and garden shrubs"></div>
    <h2 class="owner-name">Daniel Trevick</h2>
    <p class="owner-role">Owner</p>
    <ul class="contact-list">
      <li>
        <svg viewBox="0 0 24 24" aria-hidden="true"><path d="M6.6 10.8a15.1 15.1 0 0 0 6.6 6.6l2.2-2.2c.3-.3.7-.4 1-.2 1.1.4 2.3.6 3.6.6.6 0 1 .4 1 1V20c0 .6-.4 1-1 1A17 17 0 0 1 3 4c0-.6.4-1 1-1h3.5c.6 0 1 .4 1 1 0 1.3.2 2.5.6 3.6.1.3 0 .7-.2 1z"/></svg>
        <span>919-555-0148</span>
      </li>
      <li>
        <svg viewBox="0 0 24 24" aria-hidden="true"><path d="M2 5h20v14H2z" opacity=".25"/><path d="M2 5h20v2l-10 6L2 7zM2 9l10 6 10-6v10H2z"/></svg>
        <span>GildedSlatworks.com</span>
      </li>
    </ul>
    <p class="service-lines">Custom Interior &amp; Exterior<br>Window Treatments<br>By Appointment</p>
  </section>
</body>
</html>
```